Employee Handbook Cover

We need an cover for our employee handbook. The handbook should convey our core values of
-Family
-Accountability
-Professionalism
Attached is our logo. Please visit our website to get a feeling for what we do at www.brivolhomeworks.com

Industry/Entity Type

Employee

```html
<!DOCTYPE html>
<html lang="en">
<head>
<meta charset="utf-8">
<title>Brivol Employee Handbook Cover</title>
<link href="https://fonts.googleapis.com/css2?family=Roboto:wght@400;700;900&family=Roboto+Condensed:wght@400&display=swap" rel="stylesheet">
<style>
  :root {
    --stage: #1a1a1a;
    --brand-blue: #1a2fb0;
    --brand-blue-deep: #0b1580;
    --brand-blue-glow: #3356e8;
    --paper: #ffffff;
    --paper-grey: #d9d9d9;
    --ink-dark: #222222;
    --photo-light: #e6e6e6;
    --photo-mid: #9a9aa2;
  }
  html, body {
    margin: 0;
    width: 1200px;
    height: 1200px;
    overflow: hidden;
    background: var(--stage);
  }
  .stage {
    position: relative;
    width: 1200px;
    height: 1200px;
  }
  .cover {
    position: absolute;
    top: 246px;
    width: 500px;
    height: 707px;
    box-shadow: 0 20px 50px rgba(0,0,0,0.55);
  }
  .cover--back { left: 70px; }
  .cover--front { left: 630px; }
  .cover svg { display: block; }
  .wordmark, .headline { font-family: 'Roboto', sans-serif; font-weight: 900; }
  .subline { font-family: 'Roboto', sans-serif; font-weight: 400; }
  .subline--strong { font-family: 'Roboto', sans-serif; font-weight: 700; }
  .contact { font-family: 'Roboto Condensed', sans-serif; font-weight: 400; }
</style>
</head>
<body>
<main class="stage">

  <!-- Back cover -->
  <section class="cover cover--back" aria-label="Handbook back cover">
    <svg width="500" height="707" viewBox="0 0 500 707">
      <defs>
        <linearGradient id="backPaper" x1="0" y1="0" x2="0" y2="1">
          <stop offset="0" stop-color="var(--paper)"/>
          <stop offset="0.6" stop-color="var(--paper-grey)"/>
          <stop offset="1" stop-color="#f2f2f2"/>
        </linearGradient>
        <linearGradient id="backBand" x1="0" y1="0" x2="0" y2="1">
          <stop offset="0" stop-color="var(--brand-blue)"/>
          <stop offset="0.7" stop-color="var(--brand-blue-deep)"/>
          <stop offset="1" stop-color="var(--brand-blue)"/>
        </linearGradient>
      </defs>
      <rect class="paper" width="500" height="707" fill="url(#backPaper)"/>
      <line x1="0" y1="110" x2="500" y2="40" stroke="#ffffff" stroke-width="3" opacity="0.8"/>
      <text class="headline" x="250" y="70" text-anchor="middle" font-size="26" fill="var(--brand-blue)">EMPLOYEE HANDBOOK</text>
      <text class="subline" x="250" y="92" text-anchor="middle" font-size="13" fill="var(--ink-dark)">Your Guide to Company's Policies and Procedures</text>

      <g class="faint-name" opacity="0.12">
        <circle cx="130" cy="335" r="26" fill="#555555"/>
        <text class="wordmark" x="168" y="354" font-size="62" fill="#555555">Brivol</text>
      </g>

      <path class="band" d="M0,540 Q260,470 500,390 L500,707 L0,707 Z" fill="url(#backBand)"/>
      <path d="M0,540 Q260,470 500,390" fill="none" stroke="#ffffff" stroke-width="3"/>
      <circle cx="6" cy="538" r="4" fill="#ffffff"/>
      <path d="M0,650 Q250,610 500,560" fill="none" stroke="var(--brand-blue-glow)" stroke-width="2" opacity="0.5"/>

      <g class="brand-lockup">
        <circle cx="62" cy="595" r="16" fill="#ffffff"/>
        <text class="wordmark" x="86" y="608" font-size="40" fill="#ffffff">Brivol</text>
      </g>

      <g class="contact" fill="#ffffff" font-size="12">
        <g transform="translate(50,640)">
          <path d="M0,2 h10 v6 h-10 z M2,0 h6 v2 h-2 z" fill="none" stroke="#ffffff" stroke-width="1"/>
          <text x="18" y="9">555.014.2290</text>
        </g>
        <g transform="translate(50,660)">
          <rect x="0" y="1" width="10" height="8" fill="none" stroke="#ffffff" stroke-width="1"/>
          <line x1="2" y1="4" x2="8" y2="4" stroke="#ffffff" stroke-width="1"/>
          <text x="18" y="9">555.014.2291</text>
        </g>
        <text x="300" y="500">Brivol Homeworks Corp.</text>
        <text x="300" y="515">4210 Harlow Ridge Rd</text>
        <text x="300" y="530">Easton, TX 78410</text>
        <g transform="translate(300,552)">
          <rect x="0" y="1" width="11" height="8" fill="none" stroke="#ffffff" stroke-width="1"/>
          <path d="M0,1 L5.5,6 L11,1" fill="none" stroke="#ffffff" stroke-width="1"/>
          <text x="18" y="9">sales@brivolhomeworks.com</text>
        </g>
        <g transform="translate(300,570)">
          <circle cx="5.5" cy="5" r="5" fill="none" stroke="#ffffff" stroke-width="1"/>
          <line x1="0.5" y1="5" x2="10.5" y2="5" stroke="#ffffff" stroke-width="1"/>
          <text x="18" y="9">www.brivolhomeworks.com</text>
        </g>
      </g>
    </svg>
  </section>

  <!-- Front cover -->
  <section class="cover cover--front" aria-label="Handbook front cover">
    <svg width="500" height="707" viewBox="0 0 500 707">
      <defs>
        <linearGradient id="frontPaper" x1="0" y1="0" x2="0" y2="1">
          <stop offset="0" stop-color="var(--paper)"/>
          <stop offset="0.6" stop-color="var(--paper-grey)"/>
          <stop offset="1" stop-color="#eeeeee"/>
        </linearGradient>
        <linearGradient id="frontBand" x1="0" y1="0" x2="0" y2="1">
          <stop offset="0" stop-color="var(--brand-blue)"/>
          <stop offset="0.65" stop-color="var(--brand-blue-deep)"/>
          <stop offset="1" stop-color="var(--brand-blue)"/>
        </linearGradient>
        <radialGradient id="photoTone" cx="0.55" cy="0.5" r="0.6">
          <stop offset="0" stop-color="var(--photo-mid)"/>
          <stop offset="1" stop-color="var(--photo-light)"/>
        </radialGradient>
      </defs>
      <rect class="paper" width="500" height="707" fill="url(#frontPaper)"/>
      <line x1="0" y1="190" x2="500" y2="120" stroke="#ffffff" stroke-width="3" opacity="0.8"/>

      <g class="brand-lockup">
        <circle cx="108" cy="104" r="26" fill="var(--brand-blue)"/>
        <text class="wordmark" x="146" y="125" font-size="64" fill="var(--brand-blue)">Brivol</text>
      </g>

      <rect class="team-photo" role="img" aria-label="Photo of a smiling team of five business professionals in suits"
            x="50" y="200" width="450" height="300" fill="url(#photoTone)" opacity="0.85"/>

      <path class="band" d="M0,500 Q240,440 500,360 L500,707 L0,707 Z" fill="url(#frontBand)"/>
      <path d="M0,500 Q240,440 500,360" fill="none" stroke="#ffffff" stroke-width="3"/>
      <circle cx="494" cy="362" r="4" fill="#ffffff"/>
      <path d="M0,640 Q250,600 500,550" fill="none" stroke="var(--brand-blue-glow)" stroke-width="2" opacity="0.5"/>

      <text class="headline" x="270" y="500" text-anchor="middle" font-size="28" fill="#ffffff">EMPLOYEE HANDBOOK</text>
      <text class="subline" x="270" y="540" text-anchor="middle" font-size="20" fill="#ffffff">Your Guide to Company's</text>
      <text class="subline--strong" x="270" y="568" text-anchor="middle" font-size="24" fill="#ffffff">Policies and Procedures</text>
    </svg>
  </section>

</main>
</body>
</html>
```